Business Cards Design for the electrical wholesaler: clean bold dynamic :)

We need a business card design that would follow our latest brand guidelines. As an electrical wholesaler we want to bring a fresh look and feel into the industry. The design should be clean bold and dynamic. It should come alive with the renewed energy of our green colour. Our grey colour should keep things balanced and complement the notion of maturity and responsibility. We employ Lato as a corporate font however are not bound by this font and we’re open to interpretation here.

Target Market(s)

Electrical contractors

Industry/Entity Type

Business

Contact Information for Business Card

Logo
Name & Surname: Halyna Dorosh
Job Title: Director of Marketing
Email: halya.dorosh@quillmail.example
Cell phone: XXX.XXX.XXXX
Address: 20517 - 87 Ave. Edmonton, AB, Canada. T6K 4N8
Business Phone: 780.555.0184
Website: www.brovix.example

Font styles to use
Other font styles liked:
• Lato

Requirements
Must have
• Logo & website
Nice to have
• Brand elements - some of them you may find in the attached Brand Guidelines (e.g. three lines on the background signifying "W")

```html
<!DOCTYPE html>
<html lang="en">
<head>
<meta charset="utf-8">
<title>Brovix Business Card</title>
<link href="https://fonts.googleapis.com/css2?family=Lato:wght@400;700;900&display=swap" rel="stylesheet">
<style>
  :root {
    --page: #d9d9d9;
    --card: #1e1f20;
    --card-edge: #2a2b2c;
    --green: #8dc63f;
    --grey-text: #cfd0d0;
    --light-strip: #e6e6e6;
    --ink: #1e1f20;
  }
  * { box-sizing: border-box; margin: 0; padding: 0; }
  html, body { width: 800px; height: 1200px; overflow: hidden; }
  body {
    background: var(--page);
    font-family: "Lato", Arial, sans-serif;
    position: relative;
  }
  .card {
    position: absolute;
    left: 50px;
    width: 700px;
    height: 400px;
    border-radius: 26px;
    background: var(--card);
    box-shadow: inset 0 0 0 1px var(--card-edge);
    overflow: hidden;
  }
  .card--front { top: 140px; }
  .card--back { top: 660px; }

  .brand { display: flex; flex-direction: column; }
  .brand__row { display: flex; align-items: center; gap: 14px; }
  .brand__mark { width: 22px; height: 22px; background: var(--green); }
  .brand__name {
    font-weight: 900;
    color: #ffffff;
    line-height: 1;
    letter-spacing: -0.5px;
  }
  .brand__tag {
    color: var(--green);
    font-weight: 700;
    text-transform: uppercase;
    letter-spacing: 1.5px;
  }

  .card--front .brand {
    position: absolute; left: 0; right: 0; top: 150px; align-items: center;
  }
  .card--front .brand__name { font-size: 78px; }
  .card--front .brand__tag { font-size: 15px; margin-top: 10px; margin-left: 36px; }

  .card--back .brand { position: absolute; left: 60px; top: 120px; }
  .card--back .brand__name { font-size: 62px; }
  .card--back .brand__mark { width: 18px; height: 18px; }
  .card--back .brand__tag { font-size: 11px; margin-top: 8px; }

  .contact { position: absolute; left: 380px; top: 110px; color: var(--grey-text); }
  .contact__name { color: var(--green); font-size: 28px; font-weight: 700; }
  .contact__title { font-size: 14px; margin-top: 4px; }
  .contact__list { list-style: none; margin-top: 22px; font-size: 14px; line-height: 1.4; }
  .contact__list li { display: flex; gap: 10px; margin-bottom: 6px; }
  .contact__list svg { flex: 0 0 12px; margin-top: 3px; }

  .footer-band { position: absolute; left: 0; bottom: 0; width: 700px; height: 70px; }
  .footer-band__url {
    position: absolute; right: 60px; bottom: 16px;
    color: var(--ink); font-size: 15px; font-weight: 700;
  }
</style>
</head>
<body>

<section class="card card--front">
  <div class="brand">
    <div class="brand__row">
      <span class="brand__mark"></span>
      <span class="brand__name">brovix</span>
    </div>
    <span class="brand__tag">Electrical Wholesalers</span>
  </div>
</section>

<section class="card card--back">
  <div class="brand">
    <div class="brand__row">
      <span class="brand__mark"></span>
      <span class="brand__name">brovix</span>
    </div>
    <span class="brand__tag">Electrical Wholesalers</span>
  </div>

  <div class="contact">
    <p class="contact__name">Halyna Dorosh</p>
    <p class="contact__title">Founder &amp; CEO</p>
    <ul class="contact__list">
      <li>
        <svg width="12" height="12" viewBox="0 0 12 12" aria-hidden="true"><path d="M2 1h3l1 3-1.5 1a6 6 0 0 0 2.5 2.5L8 6l3 1v3a1 1 0 0 1-1 1A9 9 0 0 1 1 2a1 1 0 0 1 1-1z" fill="var(--green)"/></svg>
        <span>780.555.0184</span>
      </li>
      <li>
        <svg width="12" height="12" viewBox="0 0 12 12" aria-hidden="true"><rect x="0.5" y="2" width="11" height="8" rx="1" fill="var(--green)"/><path d="M1 3l5 4 5-4" stroke="var(--card)" stroke-width="1.2" fill="none"/></svg>
        <span>halya.dorosh@quillmail.example</span>
      </li>
      <li>
        <svg width="12" height="12" viewBox="0 0 12 12" aria-hidden="true"><path d="M6 0.5a4 4 0 0 1 4 4c0 3-4 7-4 7s-4-4-4-7a4 4 0 0 1 4-4z" fill="var(--green)"/><circle cx="6" cy="4.5" r="1.4" fill="var(--card)"/></svg>
        <span>20517 - 87 Ave. Edmonton,<br>AB, Canada. T6K 4N8</span>
      </li>
    </ul>
  </div>

  <svg class="footer-band" viewBox="0 0 700 70" aria-hidden="true">
    <polygon points="0,52 330,52 318,70 0,70" fill="var(--light-strip)"/>
    <polygon points="350,14 700,14 700,70 310,70" fill="var(--green)"/>
  </svg>
  <span class="footer-band__url">www.brovix.example</span>
</section>

</body>
</html>
```